Visitenkarten-Design für Boutique-Unternehmensberatung
Zielgruppe
Boutique Unternehmensberatung für die Chemische Industrie. Wir unterstützen Unternehmen, die Beziehung zu Ihren Händlern zu optimieren.
Vorläufige Website vertriebsbruecke-online.de kann ggf weitere Einblicke geben. Hinweis: Diese Website wurde bisher noch nicht professionell erstellt.
Aufgabenstellung
Die Visitenkarte sollte vertrauenserweckend und seriös wirken. Zeitgleich aber auch modern.

```html
<!DOCTYPE html>
<html lang="de">
<head>
<meta charset="utf-8">
<title>Aurel Beratung – Visitenkarte</title>
<link href="https://fonts.googleapis.com/css2?family=Montserrat:wght@400;500;700&display=swap" rel="stylesheet">
<style>
  :root {
    --backdrop: #565868;
    --brand-blue: #005a96;
    --card-white: #ececec;
    --ink: #2a2c30;
    --rule-dark: #252a28;
  }
  * { margin: 0; padding: 0; box-sizing: border-box; }
  html, body {
    width: 1200px; height: 1086px; overflow: hidden;
    background: var(--backdrop);
    font-family: "Montserrat", sans-serif;
  }
  .card {
    position: absolute; left: 290px;
    width: 620px; height: 365px;
    border-radius: 34px; overflow: hidden;
  }
  .card-front { top: 140px; background: var(--brand-blue); }
  .card-back { top: 580px; background: var(--card-white); }

  .wordmark {
    font-weight: 700; line-height: 1; white-space: nowrap;
  }
  .card-front .wordmark {
    position: absolute; left: 50%; top: 50%;
    transform: translate(-50%, -50%);
    color: #fff; font-size: 34px;
  }
  .card-back .wordmark {
    position: absolute; left: 58px; top: 132px;
    color: var(--brand-blue); font-size: 26px;
  }

  .person { position: absolute; right: 60px; top: 52px; text-align: left; }
  .person-name { color: var(--brand-blue); font-weight: 700; font-size: 22px; }
  .person-role { color: var(--ink); font-size: 15px; font-weight: 400; margin-top: 2px; }

  .contact-list {
    position: absolute; right: 28px; top: 138px;
    list-style: none; font-size: 13px; color: var(--ink);
  }
  .contact-list li {
    display: flex; justify-content: flex-end; align-items: center;
    gap: 14px; height: 24px;
  }
  .contact-list svg { width: 15px; height: 15px; fill: var(--brand-blue); }

  .address {
    position: absolute; left: 70px; top: 252px;
    display: flex; align-items: center; gap: 16px;
    font-size: 13.5px; color: var(--ink); line-height: 1.55;
  }
  .address svg { width: 14px; height: 18px; fill: var(--brand-blue); }

  .accent-rule {
    position: absolute; left: 0; bottom: 12px;
    width: 410px; height: 6px; background: var(--rule-dark);
  }
  .accent-band {
    position: absolute; right: 0; bottom: 0;
    width: 220px; height: 74px;
    background: var(--brand-blue);
    border-top-left-radius: 30px;
  }
</style>
</head>
<body>

<section class="card card-front">
  <div class="wordmark">Aurel Beratung</div>
</section>

<section class="card card-back">
  <div class="wordmark">Aurel Beratung</div>

  <div class="person">
    <div class="person-name">Lena Hartwig</div>
    <div class="person-role">HR manager</div>
  </div>

  <ul class="contact-list">
    <li>04521 - 38612 00
      <svg viewBox="0 0 24 24" aria-hidden="true"><path d="M6.6 10.8a15 15 0 0 0 6.6 6.6l2.2-2.2c.3-.3.7-.4 1-.2 1.1.4 2.3.6 3.6.6.6 0 1 .4 1 1V20c0 .6-.4 1-1 1A17 17 0 0 1 3 4c0-.6.4-1 1-1h3.5c.6 0 1 .4 1 1 0 1.3.2 2.5.6 3.6.1.3 0 .7-.2 1z"/></svg>
    </li>
    <li>04521 - 38612 99
      <svg viewBox="0 0 24 24" aria-hidden="true"><path d="M6 2h12v5H6zM4 8h16a2 2 0 0 1 2 2v7h-4v5H6v-5H2v-7a2 2 0 0 1 2-2zm4 9v3h8v-3z"/></svg>
    </li>
    <li>info@vertriebsbruecke-online.de
      <svg viewBox="0 0 24 24" aria-hidden="true"><path d="M12 2a10 10 0 1 0 0 20 10 10 0 0 0 0-20zm6.9 6h-3a15 15 0 0 0-1.3-3.9A8 8 0 0 1 18.9 8zM12 4c.8 1.2 1.5 2.5 1.9 4h-3.8c.4-1.5 1.1-2.8 1.9-4zM4.3 14a8 8 0 0 1 0-4h3.4a16 16 0 0 0 0 4zm.8 2h3a15 15 0 0 0 1.3 3.9A8 8 0 0 1 5.1 16zm3-8h-3a8 8 0 0 1 4.3-3.9C8.8 5.3 8.4 6.6 8.1 8zM12 20c-.8-1.2-1.5-2.5-1.9-4h3.8c-.4 1.5-1.1 2.8-1.9 4zm2.3-6H9.7a14 14 0 0 1 0-4h4.6a14 14 0 0 1 0 4zm.3 5.9c.6-1.2 1-2.5 1.3-3.9h3a8 8 0 0 1-4.3 3.9zm1.7-5.9a16 16 0 0 0 0-4h3.4a8 8 0 0 1 0 4z"/></svg>
    </li>
  </ul>

  <div class="address">
    <svg viewBox="0 0 14 18" aria-hidden="true"><path d="M7 0a7 7 0 0 0-7 7c0 5 7 11 7 11s7-6 7-11a7 7 0 0 0-7-7zm0 9.5A2.5 2.5 0 1 1 7 4.5a2.5 2.5 0 0 1 0 5z"/></svg>
    <span>Am Lindenhof 12<br>26123 Sandstedt</span>
  </div>

  <div class="accent-rule"></div>
  <div class="accent-band"></div>
</section>

</body>
</html>
```